Lantern Petals Website v.1 - attract floral shop franchisees

I need a simple information website for my new business. We are a franchisor of flower shops. The overall purpose of the website is to promote the company and the service, especially to potential franchisees and retailers. Only about 4 pages are required including homepage, About, For Supermarkets, For Franchisees, and Contact. No special functions are required except the site will have two separate inquiry forms that must be filled out online and submitted via automated email. Similarly, an email form should be linked from the Contact page. I have a logo and business cards designed by ArtMingle, and I would like the site to have a consistent color scheme and style. The key to design will be to express the joy and love associated with flowers and floral bouquets.
IMPORTANT - I will be exporting the website design to Wordpress CMS in a site hosted by HostNimbus. For smooth integration into WordPress hosted by HostNimbus, the designer should build the site using a WordPress-friendly format. Ideally, they should use HTML, CSS, and PHP. Creating a custom theme or using a page builder that exports to WordPress-compatible files is best. This ensures the site can be easily imported and managed within WordPress.

Target Market(s)

Potential franchisees (existing florists or creative types who might like to own a floral business) and supermarkets who might want us to run their floral department

Industry/Entity Type

Floral retailing

Requirements
Must have
• A brand theme that is beautiful, consistent throughout and builds on the logo design
Nice to have
• Show gender and ethnic diversity in customers and florists. Pictures of happy florists (for franchisees) and pictures of amazing floral department displays (for supermarkets)

```html
<!DOCTYPE html>
<html lang="en">
<head>
<meta charset="utf-8">
<title>Lantern Petals — Franchisor of Flower Shops</title>
<link href="https://fonts.googleapis.com/css2?family=Poppins:wght@400;500;600&family=Great+Vibes&display=swap" rel="stylesheet">
<style>
:root{
  --green:#16913f;
  --orange:#f29a22;
  --mint:#d3ede0;
  --ink:#2b2b2b;
  --text:#333333;
  --grey:#ebebeb;
  --footer:#262626;
  --white:#ffffff;
}
*{margin:0;padding:0;box-sizing:border-box}
html,body{width:1200px;height:3607px;overflow:hidden}
body{position:relative;font-family:"Poppins",sans-serif;color:var(--text);background:var(--white)}
.scene{position:absolute;left:0;top:0}
.abs{position:absolute}
.site-header{position:absolute;left:0;top:0;width:1200px;height:118px;background:var(--white);display:flex;align-items:center}
.brand{position:absolute;left:72px;top:36px;display:flex;align-items:center;gap:12px;font-family:"Poppins",sans-serif;font-weight:500;font-size:28px;color:var(--orange)}
.brand-dot{width:40px;height:40px;border-radius:50%;border:3px solid var(--orange)}
.main-nav a{position:absolute;top:50px;font-size:14px;color:var(--ink);text-decoration:none;letter-spacing:.2px}
.main-nav a.active{color:var(--green);font-weight:600}
.btn{display:inline-flex;align-items:center;justify-content:center;height:49px;border-radius:25px;background:var(--orange);color:var(--white);font-weight:600;font-size:14px;text-decoration:none;letter-spacing:.2px}
.btn-green{background:var(--green)}
.btn-outline{box-shadow:0 0 0 3px var(--white)}
.hero-title{position:absolute;left:76px;top:228px;color:var(--white);line-height:1}
.hero-title .script{display:block;font-family:"Great Vibes",cursive;font-size:118px}
.hero-title .caps{display:block;font-size:78px;font-weight:400;margin-top:-10px;letter-spacing:1px}
.hero-sub{position:absolute;left:78px;top:428px;width:400px;color:var(--white);font-size:33px;line-height:38px;letter-spacing:.5px}
.section-heading{font-size:45px;font-weight:400;color:var(--ink);letter-spacing:.5px;line-height:1}
.section-heading .accent-o{color:var(--orange)}
.section-heading .accent-g{color:var(--green)}
.welcome{font-family:"Great Vibes",cursive;font-size:44px;color:var(--green);line-height:1}
.copy p{font-size:15px;line-height:27.3px;margin-bottom:10px}
.footer-nav a{position:absolute;top:3441px;color:var(--white);font-size:14px;text-decoration:none}
.copyright{position:absolute;left:0;width:1200px;top:3485px;text-align:center;color:var(--white);font-size:12px}
.social{position:absolute;left:0;width:1200px;top:3532px;display:flex;justify-content:center;gap:14px}
.social a{color:var(--white);font-size:12px;text-decoration:none}
.footer-brand{position:absolute;left:0;width:1200px;top:3360px;display:flex;justify-content:center;align-items:center;gap:12px;color:var(--orange);font-weight:500;font-size:28px}
</style>
</head>
<body>

<svg class="scene" width="1200" height="3607" viewBox="0 0 1200 3607" aria-hidden="false">
  <defs>
    <linearGradient id="heroBg" x1="0" y1="0" x2="1" y2="1">
      <stop offset="0" stop-color="#676d78"/><stop offset="1" stop-color="#a4a8ae"/>
    </linearGradient>
    <radialGradient id="bouquet" cx=".5" cy=".45" r=".55">
      <stop offset="0" stop-color="#f6c9c4"/><stop offset=".6" stop-color="#eeb3a8"/><stop offset="1" stop-color="#c9a884"/>
    </radialGradient>
    <radialGradient id="meadow" cx=".5" cy=".5" r=".6">
      <stop offset="0" stop-color="#f1e6c2"/><stop offset=".6" stop-color="#7fa86a"/><stop offset="1" stop-color="#3f79b8"/>
    </radialGradient>
    <radialGradient id="shop1" cx=".5" cy=".55" r=".6">
      <stop offset="0" stop-color="#d9c2a8"/><stop offset=".6" stop-color="#9aa760"/><stop offset="1" stop-color="#e8eef0"/>
    </radialGradient>
    <radialGradient id="shop2" cx=".5" cy=".6" r=".6">
      <stop offset="0" stop-color="#c9b5da"/><stop offset=".55" stop-color="#6fa2c8"/><stop offset="1" stop-color="#eef1f4"/>
    </radialGradient>
  </defs>

  <!-- hero -->
  <rect x="0" y="118" width="1200" height="800" fill="url(#heroBg)"/>
  <g role="img" aria-label="Photo: bouquet of pink and cream roses wrapped in kraft paper">
    <ellipse cx="880" cy="470" rx="440" ry="340" fill="url(#bouquet)"/>
  </g>
  <path d="M0,860 C220,690 520,790 800,805 C960,812 1100,760 1200,700 L1200,3607 L0,3607 Z" fill="var(--white)"/>
  <path d="M-10,840 C210,700 520,790 800,800 C930,805 1000,795 1040,788" fill="none" stroke="var(--orange)" stroke-width="26"/>
  <path d="M-10,900 C220,755 540,830 800,820 C900,816 980,808 1030,800" fill="none" stroke="var(--green)" stroke-width="22"/>

  <!-- about -->
  <circle cx="361" cy="1148" r="233" fill="none" stroke="var(--green)" stroke-width="7"/>
  <g role="img" aria-label="Photo: bees and butterflies on daisies in a meadow">
    <circle cx="367" cy="1142" r="224" fill="url(#meadow)"/>
  </g>
  <rect x="20" y="950" width="140" height="350" rx="20" fill="var(--green)" opacity=".12" role="img" aria-label="Illustration: cartoon bee with dashed flight trail"/>
  <rect x="1020" y="1310" width="180" height="230" rx="20" fill="var(--orange)" opacity=".15" role="img" aria-label="Illustration: honeycomb flower on green stem"/>

  <!-- supermarkets band -->
  <path d="M0,1440 C300,1560 700,1440 1000,1470 C1100,1480 1160,1520 1200,1560 L1200,2130 C1000,2260 700,2190 400,2230 C200,2260 80,2300 0,2320 Z" fill="var(--mint)"/>
  <path d="M-10,1400 C250,1530 650,1440 980,1460" fill="none" stroke="var(--green)" stroke-width="22"/>
  <path d="M-10,1450 C260,1580 680,1470 1030,1500" fill="none" stroke="var(--orange)" stroke-width="26"/>
  <path d="M1210,2130 C1000,2250 720,2190 420,2200 C300,2205 220,2210 160,2220" fill="none" stroke="var(--green)" stroke-width="22"/>
  <path d="M1210,2190 C1000,2310 720,2260 420,2265 C300,2268 220,2272 170,2278" fill="none" stroke="var(--orange)" stroke-width="26"/>
  <circle cx="837" cy="1883" r="233" fill="none" stroke="var(--green)" stroke-width="7"/>
  <g role="img" aria-label="Photo: smiling florist in a green apron arranging tulips">
    <circle cx="831" cy="1877" r="224" fill="url(#shop1)"/>
  </g>
  <rect x="1040" y="1690" width="150" height="350" rx="20" fill="var(--green)" opacity=".12" role="img" aria-label="Illustration: cartoon bee with dashed flight trail"/>
  <rect x="0" y="2060" width="170" height="240" rx="20" fill="var(--orange)" opacity=".15" role="img" aria-label="Illustration: honeycomb flower on green stem"/>

  <!-- franchisees -->
  <circle cx="361" cy="2611" r="233" fill="none" stroke="var(--green)" stroke-width="7"/>
  <g role="img" aria-label="Photo: florist on the phone holding a lavender bouquet">
    <circle cx="367" cy="2605" r="224" fill="url(#shop2)"/>
  </g>
  <rect x="20" y="2415" width="140" height="350" rx="20" fill="var(--green)" opacity=".12" role="img" aria-label="Illustration: cartoon bee with dashed flight trail"/>

  <!-- contact -->
  <rect x="0" y="2912" width="1200" height="500" fill="var(--grey)"/>
  <rect x="1020" y="3080" width="180" height="220" rx="20" fill="var(--orange)" opacity=".15" role="img" aria-label="Illustration: honeycomb flower on green stem"/>
  <path d="M0,3190 C260,3330 700,3230 1000,3270 C1100,3283 1160,3300 1200,3320 L1200,3607 L0,3607 Z" fill="var(--white)"/>
  <path d="M0,3240 C260,3380 700,3280 1000,3320 C1100,3333 1160,3345 1200,3360 L1200,3607 L0,3607 Z" fill="var(--footer)"/>
  <path d="M-10,3140 C260,3280 680,3200 1040,3235" fill="none" stroke="var(--green)" stroke-width="22"/>
  <path d="M-10,3195 C260,3335 680,3250 1060,3290" fill="none" stroke="var(--orange)" stroke-width="26"/>
</svg>

<header class="site-header">
  <div class="brand"><span class="brand-dot"></span>Lantern Petals</div>
  <nav class="main-nav">
    <a class="active" href="#" style="left:354px">HOME</a>
    <a href="#" style="left:432px">ABOUT US</a>
    <a href="#" style="left:538px">FOR SUPERMARKETS</a>
    <a href="#" style="left:714px">FOR FRANCHISEES</a>
    <a href="#" style="left:876px">CONTACT</a>
  </nav>
  <a class="btn abs" href="#" style="left:976px;top:38px;width:150px;height:44px">INQUIRY NOW</a>
</header>

<section class="hero">
  <h1 class="hero-title"><span class="script">Lantern</span><span class="caps">PETALS</span></h1>
  <p class="hero-sub">We are a franchisor of flower shops.</p>
  <a class="btn btn-outline abs" href="#" style="left:78px;top:538px;width:150px;height:40px">INQUIRY NOW</a>
  <a class="btn btn-green btn-outline abs" href="#" style="left:241px;top:538px;width:148px;height:40px">CONTACT US</a>
</section>

<section class="about">
  <div class="abs" style="left:616px;top:920px;width:540px">
    <div class="welcome">Welcome</div>
    <h2 class="section-heading" style="margin-top:6px">ABOUT <span class="accent-o">LANTERN</span> <span class="accent-g">PETALS</span></h2>
  </div>
  <div class="copy abs" style="left:616px;top:1034px;width:520px">
    <p>Fresh flowers convey beauty and love, and in our view should become something every person regularly enjoys. Lantern Petals is an entrepreneurial company created to make top quality fresh flowers and professionally-designed bouquets accessible to every consumer at affordable prices.</p>
    <p>Professional florists typically sell the finest quality stems, design the most beautiful bouquets and provide the finest customer service, but their costs –of floral products, retail spaces, labor and marketing – force them to pass high prices along to customers.</p>
  </div>
  <a class="btn abs" href="#" style="left:616px;top:1312px;width:164px">READ MORE</a>
</section>

<section class="supermarkets">
  <h2 class="section-heading abs" style="left:77px;top:1716px">FOR <span class="accent-g">SUPERMARKETS</span></h2>
  <div class="copy abs" style="left:77px;top:1779px;width:500px">
    <p>Lantern Petals works with some of the country’s largest and most progressive supermarkets to provide franchisee ownership and operation of their strategically important floral departments. Supermarkets find that Lantern Petals is able to improve their financial outcomes, provide attentive customer service and satisfaction, and lift the quality of the entire store environment.</p>
  </div>
  <a class="btn abs" href="#" style="left:77px;top:1992px;width:164px">READ MORE</a>
</section>

<section class="franchisees">
  <h2 class="section-heading abs" style="left:615px;top:2427px">FOR <span class="accent-g">FRANCHISEES</span></h2>
  <div class="copy abs" style="left:615px;top:2490px;width:510px">
    <p>Lantern Petals brings the best of professional florists and supermarkets together for the benefit of consumers. It supports a national network of owner-operator franchisees, who in many cases are multi-site professional florists, with comprehensive services to enhance franchise profitability. Lantern Petals works with some of the country’s largest and most progressive supermarkets to provide franchisee ownership and operation of their strategically important floral departments.</p>
  </div>
  <a class="btn abs" href="#" style="left:615px;top:2733px;width:164px">READ MORE</a>
</section>

<section class="contact">
  <h2 class="section-heading abs" style="left:0;width:1200px;text-align:center;top:2995px">CONTACT <span class="accent-g">US</span></h2>
  <a class="btn abs" href="#" style="left:199px;top:3069px;width:386px;font-size:13px">NEW FLORIST FRANCHISE INQUIRY</a>
  <a class="btn abs" href="#" style="left:617px;top:3069px;width:388px;font-size:13px">PROFESSIONAL FLORIST FRANCHISE INQUIRY</a>
</section>

<footer class="site-footer">
  <div class="footer-brand"><span class="brand-dot"></span>Lantern Petals</div>
  <nav class="footer-nav">
    <a href="#" style="left:279px">HOME</a>
    <a href="#" style="left:367px">ABOUT US</a>
    <a href="#" style="left:486px">FOR SUPERMARKETS</a>
    <a href="#" style="left:675px">FOR FRANCHISEES</a>
    <a href="#" style="left:850px">CONTACT</a>
  </nav>
  <p class="copyright">Copyright © 2024 Company Name All Rights Reserved.</p>
  <div class="social">
    <a href="#">Circlebook</a><a href="#">Chirper</a><a href="#">Photogrid</a><a href="#">ProLink</a><a href="#">Vidstream</a>
  </div>
</footer>

</body>
</html>
```